Bramblewood Card Company Business Cards

We are a trading card store with Glimmorax, sports and other TCG cards, we need a business card design that encompasses a clean cut, modern style with a retro flare. website is bramblewoodcardco.com for reference. Can utilize a comic book era feel or a more modern outdoor feel to utilize the "Pacific Northwest" elements of tress, mountains, etc.

Industry/Entity Type

Trading cards and collectibles

Contact Information for Business Card

business name, email address, phone number, name, owner job title

Font styles to use
Sans Serif

```html
<!DOCTYPE html>
<html lang="en">
<head>
<meta charset="utf-8">
<title>Bramblewood Card Company – Business Card</title>
<link rel="stylesheet" href="https://fonts.googleapis.com/css2?family=Montserrat:wght@400;500;600;800&display=swap">
<style>
  :root {
    --backdrop: #e4e2e3;
    --card-light: #ffffff;
    --card-dark: #000000;
    --accent: #1bbde0;
    --brand-grey: #7c7c7c;
    --ink: #1a1a1a;
  }
  * { margin: 0; padding: 0; box-sizing: border-box; }
  html, body {
    width: 1200px; height: 1108px; overflow: hidden;
    background: var(--backdrop);
    font-family: "Montserrat", sans-serif;
    color: var(--ink);
  }
  .card {
    position: absolute; left: 217px; width: 766px; height: 468px;
  }
  .card--front { top: 56px; background: var(--card-light); }
  .card--back { top: 576px; height: 450px; background: var(--card-dark); }

  .brand-mark {
    position: absolute; left: 128px; top: 176px; width: 200px;
    text-align: center; color: var(--brand-grey);
    font-weight: 800; font-size: 22px; line-height: 1.15; letter-spacing: 0.02em;
    text-transform: uppercase;
  }
  .brand-mark__dot {
    display: block; width: 18px; height: 18px; margin: 0 auto 10px;
    background: var(--accent);
  }

  .divider {
    position: absolute; left: 352px; top: 174px; width: 2px; height: 148px;
    background: var(--accent);
  }
  .contact { position: absolute; left: 370px; top: 168px; }
  .contact__name {
    color: var(--accent); font-weight: 600; font-size: 30px; line-height: 1.1;
  }
  .contact__title { font-size: 17px; margin-top: 2px; }
  .contact__list { list-style: none; margin-top: 16px; font-size: 17px; }
  .contact__list li { display: flex; align-items: center; height: 28px; }
  .contact__list li + li { margin-top: 2px; }
  .contact__list svg { width: 17px; height: 17px; margin-right: 10px; fill: var(--accent); flex: none; }

  .address {
    position: absolute; left: 0; right: 0; top: 411px;
    text-align: center; font-size: 17px;
  }

  .back-mark {
    position: absolute; left: 0; right: 0; top: 170px;
    text-align: center; color: var(--brand-grey);
    font-weight: 800; font-size: 40px; line-height: 1.15; letter-spacing: 0.03em;
    text-transform: uppercase;
  }
  .back-mark__dot {
    display: block; width: 28px; height: 28px; margin: 0 auto 16px;
    background: var(--accent);
  }
</style>
</head>
<body>
  <section class="card card--front">
    <div class="brand-mark"><span class="brand-mark__dot"></span>Bramblewood Card Company</div>
    <div class="divider"></div>
    <div class="contact">
      <h1 class="contact__name">Corin Hale</h1>
      <p class="contact__title">Owner</p>
      <ul class="contact__list">
        <li>
          <svg viewBox="0 0 24 24" aria-hidden="true"><path d="M6.6 10.8a15.1 15.1 0 0 0 6.6 6.6l2.2-2.2a1 1 0 0 1 1-.25 11.4 11.4 0 0 0 3.6.57 1 1 0 0 1 1 1V20a1 1 0 0 1-1 1A17 17 0 0 1 3 4a1 1 0 0 1 1-1h3.5a1 1 0 0 1 1 1c0 1.25.2 2.45.57 3.57a1 1 0 0 1-.25 1z"/></svg>
          06-48213957
        </li>
        <li>
          <svg viewBox="0 0 24 24" aria-hidden="true"><path d="M2 5h20v14H2z M2 5l10 8 10-8" fill="none" stroke="#1bbde0" stroke-width="2"/><path d="M2 5h20l-10 8z"/></svg>
          info@bramblewoodcardcompany.com
        </li>
        <li>
          <svg viewBox="0 0 24 24" aria-hidden="true"><circle cx="12" cy="12" r="9" fill="none" stroke="#1bbde0" stroke-width="2"/><path d="M3 12h18M12 3c3 3 3 15 0 18M12 3c-3 3-3 15 0 18" fill="none" stroke="#1bbde0" stroke-width="1.6"/></svg>
          www.bramblewoodcardcompany.com
        </li>
      </ul>
    </div>
    <p class="address">2840 Alder Ridge Rd Suite 210 Tacoma, Washington 98402</p>
  </section>

  <section class="card card--back">
    <div class="back-mark"><span class="back-mark__dot"></span>Bramblewood<br>Card Company</div>
  </section>
</body>
</html>
```